New Business Card Design Project

Need a design that will create an impact / strong impression towards our clients for our business. We are in the lighting business and we do lighting retrofits for large commercial to industrial clientele.

Target Market(s)

Lighting Industry

Industry/Entity Type

Business

Font styles to use
Other font styles liked:
• we would like to use the font on our logo, not sure what it is though..

Requirements
Must have
• Our logo.
Nice to have
• We are open to suggestions that have to do with lighting.

```html
<!DOCTYPE html>
<html lang="en">
<head>
<meta charset="utf-8">
<title>Lumenvale Retrofit Co. — Business Card</title>
<link rel="stylesheet" href="https://fonts.googleapis.com/css2?family=Roboto:wght@400;500;700&display=swap">
<style>
  :root {
    --backdrop: #5a4637;
    --paper: #f2f2f1;
    --forest: #0e3a10;
    --forest-back: #0e3710;
    --accent-green: #0f7a3a;
    --name-green: #1f9146;
    --title-green: #5dbd5a;
    --brand-dark: #0e3a10;
    --white: #ffffff;
  }
  * { margin: 0; padding: 0; box-sizing: border-box; }
  html, body { width: 1200px; height: 960px; overflow: hidden; }
  body {
    background: var(--backdrop);
    font-family: "Roboto", Arial, sans-serif;
    position: relative;
  }
  .card { position: absolute; width: 600px; height: 343px; }
  .card-front { left: 314px; top: 113px; background: var(--paper); }
  .card-back { left: 311px; top: 472px; background: var(--forest-back); }

  .side-stripe {
    position: absolute; left: 0; top: 51px; width: 14px; height: 240px;
    background: var(--accent-green);
  }
  .brand {
    position: absolute; display: flex; align-items: center;
    font-weight: 700; white-space: nowrap;
  }
  .brand-mark { flex: none; }
  .card-front .brand {
    left: 54px; width: 240px; top: 158px; gap: 10px;
    font-size: 21px; line-height: 28px; color: var(--brand-dark);
  }
  .card-front .brand-mark { width: 18px; height: 18px; background: var(--title-green); }

  .contact-panel {
    position: absolute; left: 333px; top: 51px; width: 267px; height: 240px;
    background: var(--forest); color: var(--white); padding: 22px 0 0 29px;
  }
  .person-name {
    font-size: 22px; font-weight: 500; color: var(--name-green);
    line-height: 26px; letter-spacing: 0.2px;
  }
  .person-title {
    font-size: 15px; font-weight: 500; color: var(--title-green);
    line-height: 20px; margin-bottom: 13px;
  }
  .address { font-size: 14.5px; line-height: 18px; margin-bottom: 6px; }
  .contact-list { list-style: none; font-size: 14.5px; }
  .contact-list li { display: flex; align-items: center; height: 19px; }
  .contact-list svg { width: 14px; height: 14px; margin-right: 9px; fill: var(--title-green); flex: none; }

  .card-back .brand {
    left: 0; right: 0; top: 132px; justify-content: center; gap: 12px;
    font-size: 30px; line-height: 40px; color: var(--white);
  }
  .card-back .brand-mark { width: 26px; height: 26px; background: var(--title-green); }
  .site-url {
    position: absolute; left: 0; right: 0; top: 282px; text-align: center;
    color: var(--white); font-size: 14.5px; letter-spacing: 2.6px;
  }
</style>
</head>
<body>
  <section class="card card-front">
    <div class="side-stripe"></div>
    <div class="brand"><span class="brand-mark"></span>Lumenvale Retrofit Co.</div>
    <div class="contact-panel">
      <p class="person-name">DANIEL HARROW</p>
      <p class="person-title">CEO/FOUNDER</p>
      <p class="address">4120 Birchwood Avenue<br>Fairview, Oregon 97024</p>
      <ul class="contact-list">
        <li><svg viewBox="0 0 16 16" aria-hidden="true"><path d="M3 1l3 3-1.5 2a9 9 0 0 0 5.5 5.5L12 10l3 3-2 2C7 15 1 9 1 3z"/></svg>503 555 0142</li>
        <li><svg viewBox="0 0 16 16" aria-hidden="true"><path d="M4 0h8v16H4zM5.5 2v10h5V2z"/></svg>503 555 0187</li>
        <li><svg viewBox="0 0 16 16" aria-hidden="true"><path d="M4 1h8v4H4zM1 6h14v7h-3v2H4v-2H1zM5 11v3h6v-3z"/></svg>503 555 0119</li>
        <li><svg viewBox="0 0 16 16" aria-hidden="true"><path d="M1 3h14v10H1zM2.5 4.5L8 9l5.5-4.5z"/></svg>daniel@lumenvale.com</li>
        <li><svg viewBox="0 0 16 16" aria-hidden="true"><circle cx="8" cy="8" r="7"/></svg>www.lumenvale.com</li>
      </ul>
    </div>
  </section>

  <section class="card card-back">
    <div class="brand"><span class="brand-mark"></span>Lumenvale Retrofit Co.</div>
    <p class="site-url">www.lumenvaleretrofit.com</p>
  </section>
</body>
</html>
```